LunaDorata
Professional
Darlene Oakhurst
Owner
Available for Philadelphia, New Jersey , and New York
LunaDorataPhotography@examplemail.com
Im looking for an elagant design... Luna Dorata means Golden Moon in italian. My co. is after my baby girl (Mila Rose)
I photograph Newborns, Babies, maternity, Children, Family's, Engagements, Pets
Baby Face Big smile
Baby Blue/color edit
Mom with Child
bridge city shot
b&w pic of child with fence
flowers with ring

```html
<!DOCTYPE html>
<html lang="en">
<head>
<meta charset="utf-8">
<title>Luna Dorata Photography – Business Card</title>
<link rel="stylesheet" href="https://fonts.googleapis.com/css2?family=Arimo:wght@400;700&display=swap">
<style>
  :root {
    --page-bg: #d9d9d9;
    --card-top: #3b3b3b;
    --card-bottom: #161616;
    --text-main: #ffffff;
    --text-soft: #e4e4e4;
    --text-muted: #bdbdbd;
    --accent-blue: #2f9bf0;
    --accent-blue-deep: #0b5fb3;
    --accent-blue-light: #7fd0ff;
  }
  * { box-sizing: border-box; margin: 0; padding: 0; }
  html, body {
    width: 1200px; height: 862px; overflow: hidden;
    background: var(--page-bg);
    font-family: "Arimo", Arial, sans-serif;
  }
  .business-card {
    position: absolute;
    left: 240px; top: 226px;
    width: 720px; height: 410px;
    border-radius: 24px;
    background: linear-gradient(180deg, var(--card-top) 0%, #262626 45%, var(--card-bottom) 100%);
    overflow: hidden;
    color: var(--text-main);
  }
  .brand {
    position: absolute; top: 34px; left: 0; width: 100%;
    text-align: center;
  }
  .brand-name {
    font-size: 58px; font-weight: 400; letter-spacing: 1px;
    color: var(--text-main); line-height: 1;
  }
  .brand-tagline {
    margin-top: 18px;
    font-size: 17px; letter-spacing: 5px;
    color: var(--text-muted);
  }
  .side-glow {
    position: absolute; top: 158px; width: 46px; height: 105px;
    background: linear-gradient(90deg, var(--accent-blue-deep), var(--accent-blue) 50%, var(--accent-blue-light));
    box-shadow: 0 0 18px rgba(47,155,240,0.6);
  }
  .side-glow--left { left: 0; }
  .side-glow--right { right: 0; transform: scaleX(-1); }
  .gallery { position: absolute; top: 134px; left: 0; width: 100%; height: 160px; }
  .gallery-photo {
    position: absolute;
    border: 2px solid #f2f2f2;
    box-shadow: 0 4px 10px rgba(0,0,0,0.6);
  }
  .gallery-photo--smile {
    left: 74px; top: 12px; width: 200px; height: 138px;
    transform: rotate(-3deg);
    background: linear-gradient(135deg, #e8c3a8, #c98f75 55%, #8e3b35);
  }
  .gallery-photo--portrait {
    left: 266px; top: 6px; width: 196px; height: 146px;
    background: linear-gradient(135deg, #dcdcdc, #8a8a8a 55%, #3c3c3c);
  }
  .gallery-photo--blue {
    left: 456px; top: 14px; width: 158px; height: 128px;
    transform: rotate(3deg);
    background: linear-gradient(135deg, #6c6c6c, #2d2d2d 50%, #2aa2e0);
  }
  .contact {
    position: absolute; top: 296px; left: 0; width: 100%;
    text-align: center;
  }
  .contact-name { font-size: 21px; font-weight: 700; color: var(--text-main); margin-bottom: 5px; }
  .contact-line { font-size: 17px; line-height: 27px; color: var(--text-soft); }
  .contact-sep { margin: 0 8px; }
</style>
</head>
<body>
  <main class="business-card">
    <header class="brand">
      <div class="brand-name">LunaDorata</div>
      <div class="brand-tagline">Photography</div>
    </header>

    <div class="side-glow side-glow--left"></div>
    <div class="side-glow side-glow--right"></div>

    <section class="gallery">
      <div class="gallery-photo gallery-photo--smile" role="img" aria-label="Colour photo of a smiling baby"></div>
      <div class="gallery-photo gallery-photo--portrait" role="img" aria-label="Black and white portrait of a young child"></div>
      <div class="gallery-photo gallery-photo--blue" role="img" aria-label="Black and white photo of a baby with a blue colour accent"></div>
    </section>

    <section class="contact">
      <div class="contact-name">Darlene Oakhurst</div>
      <div class="contact-line">Philadelphia, New Jersey, and New York.</div>
      <div class="contact-line">Phone: 215-555-0148. Cell: 215-555-0193.</div>
      <div class="contact-line">Email: Darlene@LunaDorata.net<span class="contact-sep">|</span>www.lunadorata.net</div>
    </section>
  </main>
</body>
</html>
```